Design and Renovation Company Luxury Business Card

I want to create a luxury business card for a Design and Renovation Firm . We will use our current logo. The company name is 528BUILDA. We do not want anything standard. We need a very unique concept.
Please see uploaded inspiration. I really like the textured paper option. I would like the card to be thick with debossing, and/or embossing options. The logo has orange in it but I would like to see the card with and without the orange. I think the orange may make the company feel less high-end. The goal is to elevate the logo not match its vibe per se of the logo. We want something very unique, not standard at all!
I would like a space for :
Logo,
Name,
Position,
Email,
Office number,
Website Address,
Business Address,
Thank you!
Have fun!
Target Market(s)
Home owners Age 35 +
Industry/Entity Type
Design and Renovation
Contact Information for Business Card
Logo, Name, Position, Email, Office number, Website Address, Business Address,.
Colors
Designer to choose colors to be used in the design.
Requirements
Must have
- A luxury designer feel. Must be black or dark grey but open to other luxury ideas.
Nice to have
- Gold, silver, black embossing or debossing. Textured paper design.
Should not have
- A cheap look and feel.

```html
<!DOCTYPE html>
<html lang="en">
<head>
<meta charset="utf-8">
<title>528BUILDA – Business Card</title>
<link rel="stylesheet" href="https://fonts.googleapis.com/css2?family=Playfair+Display:wght@600&family=Poppins:wght@400;500&display=swap">
<style>
  :root {
    --backdrop: #141313;
    --matte-gold: #b88a5f;
    --matte-gold-dark: #a97b51;
    --polish-light: #f6c99c;
    --polish-mid: #e2a878;
    --polish-deep: #9a6238;
    --ink-deep: #3b220f;
    --ink-soft: #6e4325;
    --edge: #d9a77a;
  }
  * { box-sizing: border-box; margin: 0; padding: 0; }
  html, body {
    width: 1200px; height: 800px; overflow: hidden;
    background: var(--backdrop);
  }
  .canvas {
    width: 1200px; height: 800px;
    display: flex; align-items: center; justify-content: center; gap: 40px;
  }
  .card {
    position: relative;
    width: 540px; height: 309px;
    border-radius: 18px;
    border: 2px solid var(--edge);
    overflow: hidden;
    box-shadow: 0 18px 40px rgba(0,0,0,.55);
  }

  /* Back: brand side */
  .card--brand {
    background:
      radial-gradient(circle at 70% 20%, rgba(255,255,255,.12), transparent 60%),
      linear-gradient(135deg, var(--matte-gold), var(--matte-gold-dark));
    display: flex; align-items: center; justify-content: center;
  }
  .brand-name {
    font-family: "Poppins", sans-serif; font-weight: 500;
    font-size: 36px; letter-spacing: 1px; color: var(--ink-deep);
  }

  /* Front: contact side */
  .card--contact {
    background: linear-gradient(120deg, var(--polish-deep) 0%, var(--polish-mid) 35%, var(--polish-light) 60%, var(--polish-mid) 100%);
  }
  .matte-band {
    position: absolute; left: 0; top: 0; width: 100%; height: 118px;
    background: linear-gradient(135deg, var(--matte-gold), var(--matte-gold-dark));
    border-bottom: 1px solid rgba(255,230,200,.5);
  }
  .header {
    position: absolute; left: 34px; top: 28px;
  }
  .header-name {
    font-family: "Poppins", sans-serif; font-weight: 500;
    font-size: 30px; letter-spacing: 1px; line-height: 1.1; color: var(--ink-deep);
  }
  .tagline {
    margin-top: 8px;
    font-family: "Poppins", sans-serif; font-weight: 500;
    font-size: 11px; letter-spacing: 2.5px; color: var(--ink-deep);
  }
  .person {
    position: absolute; left: 34px; top: 146px;
  }
  .person-name {
    font-family: "Playfair Display", serif; font-weight: 600;
    font-size: 32px; line-height: 1.1; letter-spacing: 2px;
    color: var(--ink-soft);
    text-shadow: 0 1px 0 rgba(255,225,190,.7), 0 -1px 0 rgba(60,30,10,.35);
  }
  .person-role {
    margin-top: 8px;
    font-family: "Poppins", sans-serif; font-weight: 500;
    font-size: 13px; letter-spacing: 2px; color: var(--ink-soft);
  }
  .contacts {
    position: absolute; left: 300px; top: 140px;
    list-style: none;
    font-family: "Poppins", sans-serif; font-size: 11.5px; line-height: 1.35;
    color: var(--ink-deep);
  }
  .contacts li { display: flex; align-items: flex-start; gap: 9px; margin-bottom: 5px; }
  .contacts svg { width: 12px; height: 12px; flex: none; margin-top: 2px; fill: none; stroke: var(--ink-deep); stroke-width: 1.6; }
</style>
</head>
<body>
<main class="canvas">

  <section class="card card--brand" aria-label="Card back">
    <span class="brand-name">528BUILDA</span>
  </section>

  <section class="card card--contact" aria-label="Card front">
    <div class="matte-band"></div>
    <div class="header">
      <p class="header-name">528BUILDA</p>
      <p class="tagline">Design and Renovation Firm</p>
    </div>

    <div class="person">
      <h1 class="person-name">HARRIET<br>J. LOWELL</h1>
      <p class="person-role">Executive Director</p>
    </div>

    <ul class="contacts">
      <li>
        <svg viewBox="0 0 24 24"><path d="M5 3h4l2 5-2.5 1.5a11 11 0 0 0 6 6L16 13l5 2v4a2 2 0 0 1-2 2A17 17 0 0 1 3 5a2 2 0 0 1 2-2z"/></svg>
        <span>555-010-4821</span>
      </li>
      <li>
        <svg viewBox="0 0 24 24"><rect x="6" y="2" width="12" height="20" rx="2"/><line x1="10" y1="18" x2="14" y2="18"/></svg>
        <span>1-800-555-0199</span>
      </li>
      <li>
        <svg viewBox="0 0 24 24"><rect x="3" y="5" width="18" height="14"/><path d="M3 5l9 8 9-8"/></svg>
        <span>info@528builda.ca</span>
      </li>
      <li>
        <svg viewBox="0 0 24 24"><circle cx="12" cy="12" r="9"/><path d="M3 12h18M12 3c3 3 3 15 0 18M12 3c-3 3-3 15 0 18"/></svg>
        <span>www.528builda.com</span>
      </li>
      <li>
        <svg viewBox="0 0 24 24"><path d="M12 22s7-7 7-12a7 7 0 0 0-14 0c0 5 7 12 7 12z"/><circle cx="12" cy="10" r="2.5"/></svg>
        <span>88 Alder Crest Way<br>Kingsford, Ontario<br>Canada K0A 2M0</span>
      </li>
    </ul>
  </section>

</main>
</body>
</html>
```